Bright Net Rally Website Design (design layout only)

We need a website design for a new nonprofit organization based in Des Moines, Iowa called Bright Net Rally. The nonprofit provides soccer training opportunities to youth soccer players looking to improve their game while also affecting the lives of the less fortunate in a positive way. While participating in the training programs the players also go out and raise money for selected charities. The organization then donates the funds. In its first 18 months we donated $10,500. We would like to see designs attempt to symbolize the mission of the nonprofit - essentially "improve you while improving someone else."

We would like to see the following features:

· A place to donate - Our intent is to have the home page linked to the donation page; a simple straight-forward process for people to give money, and make donating as painless as possible - no account needed to make a donation, credit card or e-check should be the only information needed to donate, and have it be on a single page.

· A photo gallery so people can browse the photo gallery to get a better understanding of our organization and a place to add videos and a calendar to show upcoming events

· A place for contact information and the profiles of directors and board members. This should include a spot showing all the charities the organization donates to. Also includes a news section/blog for comments and suggestions.

We want the design to revolve around the content and mission. We would really like to stress our organization as nonprofit. We would also like if the website was user friendly and easy to navigate.

The logo of our organization is uploaded

```html
<!DOCTYPE html>
<html lang="en">
<head>
<meta charset="utf-8">
<title>Bright Net Rally</title>
<link href="https://fonts.googleapis.com/css2?family=Oswald:wght@400;500&family=Pathway+Gothic+One&display=swap" rel="stylesheet">
<style>
:root{
  --green-dark:#4a6b2e;
  --green-mid:#7fa24f;
  --green-text:#55772f;
  --slate:#6e6e70;
  --ink:#5a5a5a;
  --white:#ffffff;
  --line:#c9c9c9;
}
*{margin:0;padding:0;box-sizing:border-box}
html,body{width:1200px;height:1200px;overflow:hidden;background:var(--white)}
body{font-family:"Pathway Gothic One",sans-serif;color:var(--ink);position:relative}
a{color:inherit}
.site-header{position:absolute;left:0;top:0;width:1200px;height:83px;background:linear-gradient(#ffffff,#efefef);border-bottom:1px solid #d5d5d5}
.brand{position:absolute;left:228px;top:14px;display:flex;align-items:center;gap:10px}
.brand-mark{width:44px;height:44px;background:var(--green-mid)}
.brand-name{font-family:"Oswald",sans-serif;font-weight:500;font-size:26px;line-height:1;color:var(--green-text);width:150px}
.social{position:absolute;left:796px;top:14px;display:flex;gap:6px}
.social span{width:18px;height:18px;background:#9b9b9b;border-radius:3px}
.search{position:absolute;left:869px;top:10px;width:106px;height:25px;border:1px solid #bdbdbd;background:#fff;font-size:15px;color:#aaa;padding:3px 0 0 24px}
.search svg{position:absolute;left:6px;top:5px}
.main-nav{position:absolute;right:226px;top:45px;display:flex;gap:16px;font-size:18px;color:var(--green-text)}
.hero{position:absolute;left:0;top:83px;width:1200px;height:377px;background:linear-gradient(160deg,#5f8a3a 0%,#4a7430 45%,#3c6226 100%)}
.hero-title{position:absolute;left:0;width:1200px;top:30px;text-align:center;font-family:"Pathway Gothic One",sans-serif;font-size:44px;color:#fff;text-shadow:1px 1px 2px #000}
.hero-copy{position:absolute;left:228px;top:92px;width:744px;text-align:center;font-size:21px;line-height:21.5px;color:#fff;text-shadow:1px 1px 2px #000}
.donate-btn{position:absolute;left:488px;top:207px;width:223px;height:59px;background:var(--green-dark);border:2px solid #fff;color:#fff;font-size:34px;text-align:center;line-height:55px}
.band{position:absolute;left:0;top:460px;width:1200px;height:160px;background:linear-gradient(#d6d6d6,#ffffff)}
.panels{position:absolute;left:225px;top:393px;width:752px;height:264px;display:flex;border:1px solid #bdbdbd}
.panel{flex:1;text-align:center;color:#fff;position:relative;border-right:2px solid #e5e5e5}
.panel:last-child{border-right:0}
.panel--events{background:var(--green-dark)}
.panel--board{background:var(--green-mid)}
.panel--charities{background:var(--slate)}
.panel svg{position:absolute;left:50%;top:14px;transform:translateX(-50%)}
.panel h2{position:absolute;top:74px;width:100%;font-family:"Pathway Gothic One",sans-serif;font-weight:400;font-size:25px}
.panel ul{position:absolute;top:120px;width:100%;list-style:none;font-size:16px;line-height:16.2px}
.panel li{text-decoration:underline}
.panel .more{position:absolute;left:50%;top:210px;transform:translateX(-50%);background:#9a9a9a;border:1px solid #fff;font-size:16px;padding:5px 10px;white-space:nowrap}
.section-title{position:absolute;display:flex;align-items:center;gap:10px;font-family:"Oswald",sans-serif;font-weight:400;font-size:30px;color:var(--slate);letter-spacing:-0.5px}
.section-title i{display:block;width:28px;height:28px;background:var(--green-mid)}
.section-title b{font-weight:400;color:var(--green-text)}
.news-item{position:absolute;left:225px;width:470px;height:85px}
.news-thumb{position:absolute;left:0;top:0;width:85px;height:84px;border:1px solid #999;background:linear-gradient(#6b8a4a,#3f6a28)}
.news-item h3{position:absolute;left:100px;top:-2px;font-weight:400;font-size:20px;color:var(--green-text);text-decoration:underline}
.news-item p{position:absolute;left:100px;top:32px;width:370px;font-size:15px;line-height:16px;color:#777}
.news-item p a{color:var(--green-text)}
.video{position:absolute;left:727px;top:750px;width:248px;height:148px;background:linear-gradient(#3c5a2a 0%,#5b7a3d 40%,#6d8650 100%);border:1px solid #555}
.small-link{position:absolute;font-size:15px;color:#666;text-decoration:underline}
.photos{position:absolute;left:727px;top:1001px;width:248px;display:grid;grid-template-columns:repeat(3,77px);gap:8px 8px}
.photos span{height:55px;border:1px solid #888;background:linear-gradient(#4f6e33,#6c9a3f)}
</style>
</head>
<body>
<header class="site-header">
  <div class="brand"><span class="brand-mark"></span><span class="brand-name">BRIGHT NET RALLY</span></div>
  <div class="social" aria-label="Social links"><span></span><span></span><span></span></div>
  <div class="search"><svg width="12" height="12" viewBox="0 0 12 12"><circle cx="5" cy="5" r="4" fill="none" stroke="#999" stroke-width="1.5"/><line x1="8" y1="8" x2="11.5" y2="11.5" stroke="#999" stroke-width="1.5"/></svg>Search</div>
  <nav class="main-nav"><span>Donate</span><span>News</span><span>Photos &amp; Videos</span><span>Events</span><span>Board Members</span><span>Charities</span><span>Contact</span></nav>
</header>

<section class="hero" role="img" aria-label="Youth soccer players in colourful kits kicking a ball on a grass field">
  <h1 class="hero-title">WELCOME TO BRIGHT NET RALLY</h1>
  <p class="hero-copy">Based in Des Moines, IA, our nonprofit organization provides soccer training opportunities to youth soccer players looking to improve their game while also affecting the lives of the less fortunate in a positive way. While participating in the training programs, players also go out and raise money for selected charities to which Bright Net Rally then donates the funds. In our first 18 months, we donated over $10,500 to charities.</p>
  <div class="donate-btn">DONATE NOW!</div>
</section>
<div class="band"></div>

<section class="panels">
  <div class="panel panel--events">
    <svg width="46" height="46" viewBox="0 0 46 46"><circle cx="23" cy="23" r="20" fill="none" stroke="#fff" stroke-width="3"/><polygon points="23,15 30,20 27.5,28 18.5,28 16,20" fill="#fff"/><line x1="23" y1="15" x2="23" y2="5" stroke="#fff" stroke-width="2"/><line x1="30" y1="20" x2="40" y2="17" stroke="#fff" stroke-width="2"/><line x1="16" y1="20" x2="6" y2="17" stroke="#fff" stroke-width="2"/><line x1="27.5" y1="28" x2="33" y2="37" stroke="#fff" stroke-width="2"/><line x1="18.5" y1="28" x2="13" y2="37" stroke="#fff" stroke-width="2"/></svg>
    <h2>UPCOMING EVENTS</h2>
    <ul><li>9/6/14 at 12 PM: Game against XXXXXX</li><li>9/13/14 at 12 PM: Game against XXXXXX</li><li>9/20/14 at 12 PM: Game against XXXXXX</li><li>9/27/14 at 12 PM: Game against XXXXXX</li></ul>
    <span class="more">More Events...</span>
  </div>
  <div class="panel panel--board">
    <svg width="48" height="46" viewBox="0 0 48 46"><circle cx="31" cy="10" r="8" fill="#fff"/><path d="M18 30 q0-12 13-12 q13 0 13 12z" fill="#fff"/><circle cx="15" cy="24" r="6" fill="#fff"/><path d="M4 42 q0-10 11-10 q11 0 11 10z" fill="#fff"/></svg>
    <h2>MEET OUR BOARD MEMBERS</h2>
    <ul><li>John Doe</li><li>Jane Doe</li><li>Bob Johnson</li><li>Rachael Smith</li></ul>
    <span class="more">All Bios...</span>
  </div>
  <div class="panel panel--charities">
    <svg width="46" height="46" viewBox="0 0 46 46"><path d="M23 2 L44 22 L38 22 L38 44 L28 44 L28 32 L18 32 L18 44 L8 44 L8 22 L2 22z" fill="#fff"/></svg>
    <h2>CHARITIES WE SUPPORT</h2>
    <ul><li>Harbor Relief Network</li><li>Bright Dreams Fund</li><li>Open Hands Co-op</li><li>Hope Street Mission</li></ul>
    <span class="more">More Charities...</span>
  </div>
</section>

<h2 class="section-title" style="left:225px;top:698px"><i></i><span><b>NEWS &amp;</b> ANNOUNCEMENTS</span></h2>

<article class="news-item" style="top:750px"><div class="news-thumb" role="img" aria-label="Soccer ball on grass"></div><h3>News Item Title Goes Here</h3><p>Lorem ipsum dolor sit amet, consectetur adipiscing elit. Praesent suscipit, mauris eget facilisis commodo, est metus rhoncus diam, at iaculis justo mauris at augue. Vestibulum fringilla mauris sed ornare feugiat. <a>Read more...</a></p></article>
<article class="news-item" style="top:864px"><div class="news-thumb" role="img" aria-label="Young players in blue kits on the field"></div><h3>News Item Title Goes Here</h3><p>Lorem ipsum dolor sit amet, consectetur adipiscing elit. Praesent suscipit, mauris eget facilisis commodo, est metus rhoncus diam, at iaculis justo mauris at augue. Vestibulum fringilla mauris sed ornare feugiat. <a>Read more...</a></p></article>
<article class="news-item" style="top:982px"><div class="news-thumb" role="img" aria-label="Goalkeeper reaching in front of the net" style="background:linear-gradient(#c8ccd0,#7d8a78)"></div><h3>News Item Title Goes Here</h3><p>Lorem ipsum dolor sit amet, consectetur adipiscing elit. Praesent suscipit, mauris eget facilisis commodo, est metus rhoncus diam, at iaculis justo mauris at augue. Vestibulum fringilla mauris sed ornare feugiat. <a>Read more...</a></p></article>
<article class="news-item" style="top:1096px"><div class="news-thumb" role="img" aria-label="Two players challenging for the ball"></div><h3>News Item Title Goes Here</h3><p>Lorem ipsum dolor sit amet, consectetur adipiscing elit. Praesent suscipit, mauris eget facilisis commodo, est metus rhoncus diam, at iaculis justo mauris at augue. Vestibulum fringilla mauris sed ornare feugiat. <a>Read more...</a></p></article>

<h2 class="section-title" style="left:724px;top:698px"><i></i><span><b>FEATURED</b> VIDEO</span></h2>
<div class="video" role="img" aria-label="Video of a youth soccer match on a wide field"></div>
<span class="small-link" style="left:727px;top:907px">View More Videos...</span>

<h2 class="section-title" style="left:724px;top:949px"><i></i><span><b>RECENT</b> PHOTOS</span></h2>
<div class="photos" role="img" aria-label="Six photos of players in pink kits during a match"><span></span><span></span><span></span><span></span><span></span><span></span></div>
<span class="small-link" style="left:727px;top:1133px">View More Photos...</span>
</body>
</html>
```